Design a web site for my business - Brightline Coatings Co.

We are a family business that handles design, fabrication and installation of powder coated aluminum, stainless steel and glass products. Including handrails, privacy slat screens, electric gates and pool fencing. We are based in the Whitsundays in North Queensland and service an area from Airlie Beach to Townsville.

Target Market(s)

Domestic and commercial

Industry/Entity Type

fabrication - manufacturing

Coding

Coded - Design and coding required

Number of Pages Required

5+ page

Colors
0054AA
0677BA
7BADD7
CADEEF
E8F1F8

Requirements
Must have
• photo galleries, contact page, one page for privacy screens, balustrades, glass fencing, stainless steel handrail, powder coated aluminium handrails and pool fencing

```html
<!DOCTYPE html>
<html lang="en">
<head>
<meta charset="utf-8">
<title>Brightline Coatings Co — Aluminium, stainless &amp; glass</title>
<link rel="stylesheet" href="https://fonts.googleapis.com/css2?family=Inter:wght@400;500;600&family=Newsreader:ital,opsz,wght@0,6..72,400;1,6..72,400&display=swap">
<style>
:root{
  --blue-deep:#0054AA;
  --blue:#0677BA;
  --blue-mid:#7BADD7;
  --blue-soft:#CADEEF;
  --blue-pale:#E8F1F8;
  --bg-tint:#F1F6FB;
  --ink:#15202E;
  --ink-soft:#4A5563;
  --ink-faint:#6B7582;
  --line:#DDE3EA;
  --white:#FFFFFF;
  --serif:"Newsreader",Georgia,serif;
  --sans:"Inter",Arial,sans-serif;
}
*{box-sizing:border-box;margin:0;padding:0}
html,body{width:1200px;height:2811px;overflow:hidden}
body{position:relative;background:var(--white);font-family:var(--sans);color:var(--ink)}
.abs{position:absolute}
.eyebrow{font-family:var(--sans);font-size:8px;font-weight:600;letter-spacing:.2em;text-transform:uppercase;color:var(--blue)}
.serif{font-family:var(--serif);font-weight:400}

/* header */
.site-header{position:absolute;left:0;top:0;width:1200px;height:50px;background:var(--white);border-bottom:1px solid var(--line)}
.brand{position:absolute;display:flex;align-items:center;gap:5px;font-family:var(--sans);font-size:8px;font-weight:600;color:var(--ink-soft);letter-spacing:.04em;text-transform:uppercase}
.brand-mark{width:10px;height:10px;background:var(--blue-mid)}
.nav{position:absolute;left:433px;top:19px;display:flex;gap:20px;font-size:9.5px;color:var(--ink-soft)}
.header-loc{position:absolute;left:782px;top:19px;font-size:9px;color:var(--ink-faint)}
.btn{display:flex;align-items:center;justify-content:center;border-radius:3px;font-size:9.5px;font-weight:500;text-decoration:none}
.btn-primary{background:linear-gradient(90deg,var(--blue-deep),var(--blue) 70%,var(--blue-mid));color:var(--white)}
.btn-ghost{background:var(--white);border:1px solid var(--blue-soft);color:var(--blue-deep)}

/* hero */
.hero{position:absolute;left:0;top:50px;width:1200px;height:550px;background:linear-gradient(180deg,var(--blue-pale),#F7FAFD 85%,var(--white))}
.hero-title{position:absolute;left:232px;top:63px;font-family:var(--serif);font-size:47px;line-height:47px;letter-spacing:-.01em;color:var(--ink)}
.hero-title em{font-style:italic;color:var(--blue-deep)}
.hero-lede{position:absolute;left:232px;top:321px;width:330px;font-size:11.5px;line-height:18.5px;color:var(--ink-soft)}
.stat{position:absolute;top:455px;width:95px}
.stat-num{font-family:var(--serif);font-size:21px;color:var(--blue-deep);line-height:24px}
.stat-label{font-size:7.5px;line-height:10px;color:var(--ink-soft);margin-top:2px}
.photo{background:linear-gradient(180deg,#AFC2D6 0%,#6D8C67 30%,#5B7C92 55%,#3E6A8E 80%,#8A5A35 100%)}
.hero-photo{position:absolute;left:615px;top:50px;width:353px;height:440px;box-shadow:0 20px 40px rgba(0,84,170,.12)}
.featured{position:absolute;left:600px;top:425px;width:131px;height:80px;background:var(--white);border-radius:3px;box-shadow:0 8px 22px rgba(21,32,46,.12);padding:11px 11px}
.featured .eyebrow{font-size:6px}
.featured-title{font-size:8.5px;font-weight:500;line-height:12px;margin-top:4px}
.featured-sub{font-size:6.8px;line-height:9.5px;color:var(--ink-faint);margin-top:3px}

/* services */
.section-title{font-family:var(--serif);font-size:31px;line-height:30px;color:var(--ink);letter-spacing:-.01em}
.services-intro{position:absolute;left:726px;top:712px;width:245px;font-size:8.7px;line-height:12.5px;color:var(--ink-soft)}
.card{position:absolute;width:235px;height:299px;border:1px solid var(--line);border-radius:2px;background:var(--white);overflow:hidden}
.card-photo{height:175px}
.card-num{position:absolute;left:15px;top:192px;right:15px;display:flex;align-items:center;gap:10px;font-family:var(--serif);font-size:9px;color:var(--blue)}
.card-num::after{content:"";flex:1;height:1px;background:var(--line)}
.card-title{position:absolute;left:15px;top:215px;font-family:var(--serif);font-size:13.5px}
.card-text{position:absolute;left:15px;top:239px;width:205px;font-size:8.5px;line-height:12.5px;color:var(--ink-soft)}
.card-link{position:absolute;left:15px;top:272px;font-size:8.5px;color:var(--blue-deep)}

/* process */
.process{position:absolute;left:0;top:1460px;width:1200px;height:556px;background:var(--bg-tint);border-top:1px solid var(--line);border-bottom:1px solid var(--line)}
.process-photo{position:absolute;left:232px;top:61px;width:347px;height:433px;background:linear-gradient(180deg,#C9D1D8 0%,#5A3F2E 40%,#7D8A90 62%,#3F6034 85%,#6B5440 100%);box-shadow:0 10px 30px rgba(21,32,46,.12)}
.step{position:absolute;left:620px;width:350px}
.step-num{position:absolute;left:0;top:-4px;font-family:var(--serif);font-size:17px;color:var(--blue)}
.step-title{margin-left:49px;font-family:var(--serif);font-size:11.5px}
.step-text{margin-left:49px;margin-top:5px;font-size:8.5px;line-height:13px;color:var(--ink-soft)}

/* area */
.area-text{position:absolute;left:232px;top:2131px;width:290px;font-size:10px;line-height:15px;color:var(--ink-soft)}
.town{position:absolute;width:204px;height:28px;border:1px solid var(--line);border-radius:2px;display:flex;align-items:center;gap:6px;padding-left:10px;font-size:8.7px;color:var(--ink)}
.town::before{content:"";width:4px;height:4px;border-radius:50%;background:var(--blue)}

/* cta */
.cta{position:absolute;left:232px;top:2276px;width:736px;height:169px;border-radius:8px;background:linear-gradient(120deg,var(--blue-deep) 0%,var(--blue) 60%,var(--blue-mid) 100%);color:var(--white)}
.cta .eyebrow{position:absolute;left:41px;top:44px;color:var(--blue-soft)}
.cta-title{position:absolute;left:40px;top:56px;font-family:var(--serif);font-size:31px}
.cta-text{position:absolute;left:41px;top:101px;width:290px;font-size:10px;line-height:15px;color:var(--blue-pale)}
.cta .btn{position:absolute;left:582px;top:68px;width:113px;height:32px;background:var(--white);color:var(--blue-deep);font-size:9px}

/* footer */
.site-footer{position:absolute;left:0;top:2566px;width:1200px;height:245px;background:var(--bg-tint);border-top:1px solid var(--line)}
.footer-about{position:absolute;left:232px;top:92px;width:280px;font-size:8.7px;line-height:14px;color:var(--ink-soft)}
.footer-region{position:absolute;left:232px;top:143px;font-size:7.5px;color:var(--ink-faint)}
.socials{position:absolute;left:232px;top:170px;display:flex;gap:25px}
.socials span{width:11px;height:11px;border:1.3px solid var(--blue-deep);border-radius:50%}
.footer-col{position:absolute;top:45px}
.footer-col ul{list-style:none;margin-top:10px}
.footer-col li{font-size:8.7px;color:var(--ink-soft);line-height:17.5px}
.contact-row{display:flex;align-items:center;gap:6px;font-size:9px;color:var(--ink-soft);margin-top:6px}
.footer-bottom{position:absolute;left:232px;top:203px;width:736px;border-top:1px solid var(--line);padding-top:15px;display:flex;justify-content:space-between;font-size:7px;color:var(--ink-faint)}
</style>
</head>
<body>

<header class="site-header">
  <div class="brand" style="left:232px;top:20px"><span class="brand-mark"></span>Brightline Coatings Co</div>
  <nav class="nav"><span>Home</span><span>Services</span><span>Gallery</span><span>Contact</span></nav>
  <div class="header-loc">Airlie Beach · QLD</div>
  <a class="btn btn-primary abs" style="left:865px;top:10px;width:103px;height:30px">Request a Quote</a>
</header>

<section class="hero">
  <div class="eyebrow abs" style="left:232px;top:42px">Whitsundays · Family Fabricators</div>
  <h1 class="hero-title serif">Aluminium,<br>stainless<br><em>&amp; glass</em> —<br>engineered<br>for the coast.</h1>
  <p class="hero-lede">We design, fabricate and install handrails, privacy screens, gates and pool fencing from Airlie Beach to Townsville. Built to last, finished to impress.</p>
  <a class="btn btn-primary abs" style="left:232px;top:392px;width:102px;height:31px">Request a quote</a>
  <a class="btn btn-ghost abs" style="left:341px;top:392px;width:103px;height:31px">Explore our work</a>
  <div class="stat" style="left:232px"><div class="stat-num">20+</div><div class="stat-label">Years combined experience</div></div>
  <div class="stat" style="left:332px"><div class="stat-num">316</div><div class="stat-label">Marine grade stainless</div></div>
  <div class="stat" style="left:431px"><div class="stat-num">QLD</div><div class="stat-label">Locally owned &amp; operated</div></div>
  <div class="hero-photo photo" role="img" aria-label="Waterfront boardwalk with powder coated aluminium handrail, palms and bay"></div>
  <div class="featured">
    <div class="eyebrow">Featured</div>
    <div class="featured-title">Marina boardwalk, Airlie Beach</div>
    <div class="featured-sub">Powder coated aluminium handrail system</div>
  </div>
</section>

<section>
  <div class="eyebrow abs" style="left:232px;top:671px">What we make</div>
  <h2 class="section-title abs" style="left:232px;top:690px">Six disciplines, one<br>workshop.</h2>
  <p class="services-intro">Every project is designed, fabricated and installed by our own team — domestic homes, commercial developments and marine environments.</p>

  <article class="card" style="left:232px;top:784px">
    <div class="card-photo" role="img" aria-label="Cream aluminium slat privacy screen gate" style="background:linear-gradient(180deg,#1E3F7A 0%,#5D7FA8 40%,#D9D3C1 60%,#B9B6AE 100%)"></div>
    <div class="card-num">01</div><h3 class="card-title">Privacy Screens</h3>
    <p class="card-text">Powder coated aluminium slat screens for privacy, style and airflow.</p>
    <a class="card-link">Learn more →</a>
  </article>
  <article class="card" style="left:482px;top:784px">
    <div class="card-photo" role="img" aria-label="Timber walkway with stainless wire balustrade among rocks and gardens" style="background:linear-gradient(160deg,#3F5A35 0%,#6E5A4A 50%,#8A8A78 100%)"></div>
    <div class="card-num">02</div><h3 class="card-title">Balustrades</h3>
    <p class="card-text">Stainless wire, tube and aluminium balustrades — engineered to code.</p>
    <a class="card-link">Learn more →</a>
  </article>
  <article class="card" style="left:733px;top:784px">
    <div class="card-photo" role="img" aria-label="Frameless glass fence beside tropical plants and paving" style="background:linear-gradient(90deg,#2F4A2C 0%,#6C8A6A 50%,#A9B4A7 100%)"></div>
    <div class="card-num">03</div><h3 class="card-title">Glass Fencing</h3>
    <p class="card-text">Frameless and semi-frameless glass for pools, terraces and stairs.</p>
    <a class="card-link">Learn more →</a>
  </article>
  <article class="card" style="left:232px;top:1100px">
    <div class="card-photo" role="img" aria-label="Timber house deck with stainless handrail and glass balustrade" style="background:linear-gradient(180deg,#4A3428 0%,#7E8A90 55%,#5E4536 100%)"></div>
    <div class="card-num">04</div><h3 class="card-title">Stainless Handrails</h3>
    <p class="card-text">Marine-grade 316 stainless — polished, brushed or blackened.</p>
    <a class="card-link">Learn more →</a>
  </article>
  <article class="card" style="left:482px;top:1100px">
    <div class="card-photo" role="img" aria-label="Waterfront boardwalk with aluminium handrail" style="background:linear-gradient(180deg,#A9BCD0 0%,#5E7C5E 35%,#4B7296 65%,#8A5A35 100%)"></div>
    <div class="card-num">05</div><h3 class="card-title">Aluminium Handrails</h3>
    <p class="card-text">Powder coated handrails in any colour, built to last coastal conditions.</p>
    <a class="card-link">Learn more →</a>
  </article>
  <article class="card" style="left:733px;top:1100px">
    <div class="card-photo" role="img" aria-label="Glass pool fence beside garden bed" style="background:linear-gradient(90deg,#2F4A2C 0%,#6C8A6A 50%,#A9B4A7 100%)"></div>
    <div class="card-num">06</div><h3 class="card-title">Pool Fencing</h3>
    <p class="card-text">Compliant pool fencing in glass or aluminium — safe and beautiful.</p>
    <a class="card-link">Learn more →</a>
  </article>
</section>

<section class="process">
  <div class="process-photo" role="img" aria-label="Two-storey timber home with stainless handrails and glass balustrade above tropical garden"></div>
  <div class="eyebrow abs" style="left:620px;top:99px">How we work</div>
  <h2 class="section-title abs" style="left:620px;top:115px">Considered from the first<br>sketch<br>to the final bolt.</h2>
  <div class="step" style="top:235px"><span class="step-num">01</span><div class="step-title">Consult &amp; measure</div><p class="step-text">We visit your site, understand the brief and take precise measurements.</p></div>
  <div class="step" style="top:288px"><span class="step-num">02</span><div class="step-title">Design &amp; quote</div><p class="step-text">You receive drawings, material specs and a fixed-price quote — no surprises.</p></div>
  <div class="step" style="top:353px"><span class="step-num">03</span><div class="step-title">Fabricate in-house</div><p class="step-text">Cut, welded, powder coated and quality checked in our Whitsundays workshop.</p></div>
  <div class="step" style="top:419px"><span class="step-num">04</span><div class="step-title">Install &amp; handover</div><p class="step-text">Clean installation by our team. Certified for pool fencing and balustrade compliance.</p></div>
</section>

<section>
  <div class="eyebrow abs" style="left:232px;top:2077px">Service area</div>
  <h2 class="section-title abs" style="left:232px;top:2093px;font-size:23px">From Airlie to Townsville.</h2>
  <p class="area-text">We're based in the Whitsundays and travel the coast for projects large and small. If you're unsure whether we cover your area — just ask.</p>
  <div class="town" style="left:551px;top:2077px">Airlie Beach</div>
  <div class="town" style="left:764px;top:2077px">Cannonvale</div>
  <div class="town" style="left:551px;top:2113px">Proserpine</div>
  <div class="town" style="left:764px;top:2113px">Bowen</div>
  <div class="town" style="left:551px;top:2150px">Collinsville</div>
  <div class="town" style="left:764px;top:2150px">Home Hill</div>
  <div class="town" style="left:551px;top:2186px">Ayr</div>
  <div class="town" style="left:764px;top:2186px">Townsville</div>
</section>

<section class="cta">
  <div class="eyebrow">Free measure &amp; quote</div>
  <h2 class="cta-title">Ready when you are.</h2>
  <p class="cta-text">Send us your plans or a photo of the space — we'll come back with a design and price.</p>
  <a class="btn">Start your project →</a>
</section>

<footer class="site-footer">
  <div class="brand" style="left:232px;top:60px"><span class="brand-mark"></span>Brightline Coatings Co</div>
  <p class="footer-about">A family business designing, fabricating and installing powder coated aluminium, stainless steel and glass — engineered for the Whitsundays coast.</p>
  <div class="footer-region">Servicing Airlie Beach to Townsville · North Queensland</div>
  <div class="socials" aria-label="Social links"><span></span><span></span><span></span></div>
  <div class="footer-col" style="left:615px">
    <div class="eyebrow">Services</div>
    <ul><li>Privacy Screens</li><li>Balustrades</li><li>Glass Fencing</li><li>Stainless Handrails</li><li>Aluminium Handrails</li><li>Pool Fencing</li></ul>
  </div>
  <div class="footer-col" style="left:806px">
    <div class="eyebrow">Contact</div>
    <div class="contact-row" style="margin-top:10px">
      <svg width="12" height="12" viewBox="0 0 24 24" fill="none" stroke="#0054AA" stroke-width="2"><path d="M5 3h4l2 5-3 2a12 12 0 0 0 6 6l2-3 5 2v4a2 2 0 0 1-2 2A18 18 0 0 1 3 5a2 2 0 0 1 2-2z"/></svg>
      XXX XXX XXXX</div>
    <div class="contact-row">
      <svg width="12" height="12" viewBox="0 0 24 24" fill="none" stroke="#0054AA" stroke-width="2"><rect x="3" y="5" width="18" height="14" rx="2"/><path d="M3 7l9 6 9-6"/></svg>
      hello@brightlinecoatings.example</div>
  </div>
  <div class="footer-bottom"><span>© 2026 Brightline Coatings Co. All rights reserved.</span><span>Design · Fabrication · Installation</span></div>
</footer>

</body>
</html>
```